Pebble Tracks - explore habits of productive people

Pebble Tracks is a social place around habits and productivity

The full brief below:

https://notes.brimwellpad.net/page/d/7Qx-RtVmPLa93KwBz-H-cNmq2YeTsRfvUdGkHpXwaB/view?mode=shared

Colors

Designer to choose colors to be used in the design.

Requirements
Must have
• - a feed page to display habits
• - a habit page to add a habit
• / clean, no cluttered design, lots of white space
• / inspired by material design or other design system
Nice to have
• - user page

```html
<!DOCTYPE html>
<html lang="en">
<head>
<meta charset="utf-8">
<title>Pebble Tracks – Feed</title>
<link rel="stylesheet" href="https://fonts.googleapis.com/css2?family=Poppins:wght@400;500;600&display=swap">
<style>
:root{
  --bar-top:#2eaae8;
  --bar-bottom:#1479b8;
  --page:#f3f3f3;
  --panel:#ffffff;
  --panel-border:#e2e2e2;
  --feed-head:#e6e6e6;
  --ink:#2b2b2b;
  --ink-soft:#3a3a3a;
  --accent:#1e8fd6;
  --white:#ffffff;
}
*{box-sizing:border-box;margin:0;padding:0}
html,body{width:1200px;height:1199px;overflow:hidden}
body{background:var(--page);font-family:"Poppins",sans-serif;color:var(--ink);position:relative}
.topbar{height:80px;background:linear-gradient(var(--bar-top),var(--bar-bottom));display:flex;align-items:center;justify-content:space-between;padding:0 52px 0 50px}
.brand{color:var(--white);font-weight:600;font-size:25px;letter-spacing:-.3px}
.account{display:flex;align-items:center;gap:10px;color:var(--white);font-size:19px}
.avatar{border-radius:50%;flex:none}
.account .avatar{width:38px;height:38px;background:radial-gradient(circle at 50% 45%,#e8b99a,#8a5a3e);border:2px solid var(--white)}
.add-btn{width:40px;height:40px;margin-left:2px}
.panel{position:absolute;left:52px;top:129px;width:1096px;height:1005px;background:var(--panel);border:1px solid var(--panel-border);box-shadow:0 1px 3px rgba(0,0,0,.06);padding:28px 25px}
.feed-title{height:54px;background:var(--feed-head);border-radius:3px;font-size:21px;font-weight:500;padding:13px 15px}
.post{position:relative;height:268px;margin-top:25px;border:1px solid #dcdcdc;box-shadow:0 1px 4px rgba(0,0,0,.12);padding:28px 22px 0}
.post+.post{margin-top:32px}
.post-head{display:flex;gap:12px;align-items:center}
.post .avatar{width:52px;height:52px}
.name{font-size:22px;font-weight:500;line-height:1.2}
.meta{font-size:14px;color:var(--ink-soft);margin-top:2px}
.info{position:absolute;right:16px;top:17px;width:20px;height:20px}
.steps{margin-top:28px;font-size:17.5px;font-weight:500;line-height:32px}
.actions{display:flex;gap:36px;margin-top:12px;color:var(--accent);font-size:16.5px;font-weight:500}
.actions span{display:flex;align-items:center;gap:10px}
.page-code{position:absolute;right:22px;bottom:20px;font-size:17px}
</style>
</head>
<body>
<header class="topbar">
  <div class="brand">PEBBLE TRACKS</div>
  <div class="account">
    <span>User Name</span>
    <div class="avatar" role="img" aria-label="User profile photo"></div>
    <svg class="add-btn" viewBox="0 0 40 40" aria-label="Add habit"><circle cx="20" cy="20" r="18" fill="none" stroke="#fff" stroke-width="2.6"/><path d="M20 10v20M10 20h20" stroke="#fff" stroke-width="2.6"/></svg>
  </div>
</header>

<main class="panel">
  <div class="feed-title">Feed:</div>

  <article class="post">
    <div class="post-head">
      <div class="avatar" role="img" aria-label="Profile photo of Clara" style="background:radial-gradient(circle at 50% 50%,#d9a88a,#5a3322)"></div>
      <div><div class="name">Clara</div><div class="meta">5 hours ago / Nemo enim ipsam voluptatem quias</div></div>
    </div>
    <svg class="info" viewBox="0 0 20 20"><circle cx="10" cy="10" r="9.5" fill="#1e8fd6"/><rect x="8.8" y="8.5" width="2.4" height="6.5" fill="#fff"/><circle cx="10" cy="5.8" r="1.4" fill="#fff"/></svg>
    <div class="steps">
      <p>After I pour my morning cup of coffee, I will meditate for sixty seconds....</p>
      <p>After I meditate for sixty seconds, I will write my to-do list for the day....</p>
      <p>After I write my to-do list for the day, I will immediately begin my first task...</p>
    </div>
    <div class="actions">
      <span><svg width="20" height="20" viewBox="0 0 20 20" fill="none" stroke="#1e8fd6" stroke-width="1.5"><path d="M1 9h4v10H1zM5 10l4-8c2 0 2.5 1.5 2 3.5L10.5 8H17c1.3 0 2 1 1.7 2.3l-1.5 6.5c-.3 1.2-1 2-2.2 2H5"/></svg>10 Likes</span>
      <span><svg width="20" height="20" viewBox="0 0 20 20" fill="none" stroke="#1e8fd6" stroke-width="1.5"><path d="M1 2h17v11h-9l-4 4v-4H1zM4 6h11M4 9h9"/></svg>50 Comments</span>
    </div>
  </article>

  <article class="post">
    <div class="post-head">
      <div class="avatar" role="img" aria-label="Profile photo of Smith" style="background:radial-gradient(circle at 50% 50%,#e4c0a6,#6b5544)"></div>
      <div><div class="name">Smith</div><div class="meta">5 hours ago / Nemo enim ipsam voluptatem quias</div></div>
    </div>
    <svg class="info" viewBox="0 0 20 20"><circle cx="10" cy="10" r="9.5" fill="#1e8fd6"/><rect x="8.8" y="8.5" width="2.4" height="6.5" fill="#fff"/><circle cx="10" cy="5.8" r="1.4" fill="#fff"/></svg>
    <div class="steps">
      <p>After I finish eating dinner, I will put my plate directly into the dishwasher...</p>
      <p>After I put my dishes away, I will immediately wipe down the counter...</p>
      <p>After I wipe down the counter, I will set out my coffee mug for tomorrow morning.</p>
    </div>
    <div class="actions">
      <span><svg width="20" height="20" viewBox="0 0 20 20" fill="none" stroke="#1e8fd6" stroke-width="1.5"><path d="M1 9h4v10H1zM5 10l4-8c2 0 2.5 1.5 2 3.5L10.5 8H17c1.3 0 2 1 1.7 2.3l-1.5 6.5c-.3 1.2-1 2-2.2 2H5"/></svg>10 Likes</span>
      <span><svg width="20" height="20" viewBox="0 0 20 20" fill="none" stroke="#1e8fd6" stroke-width="1.5"><path d="M1 2h17v11h-9l-4 4v-4H1zM4 6h11M4 9h9"/></svg>50 Comments</span>
    </div>
  </article>

  <article class="post">
    <div class="post-head">
      <div class="avatar" role="img" aria-label="Profile photo of Ranette" style="background:radial-gradient(circle at 50% 50%,#efcfae,#8c6440)"></div>
      <div><div class="name">Ranette</div><div class="meta">5 hours ago / Nemo enim ipsam voluptatem quias</div></div>
    </div>
    <svg class="info" viewBox="0 0 20 20"><circle cx="10" cy="10" r="9.5" fill="#1e8fd6"/><rect x="8.8" y="8.5" width="2.4" height="6.5" fill="#fff"/><circle cx="10" cy="5.8" r="1.4" fill="#fff"/></svg>
    <div class="steps">
      <p>After I pour my morning cup of coffee, I will meditate for sixty seconds....</p>
      <p>After I meditate for sixty seconds, I will write my to-do list for the day....</p>
      <p>After I write my to-do list for the day, I will immediately begin my first task...</p>
    </div>
    <div class="actions">
      <span><svg width="20" height="20" viewBox="0 0 20 20" fill="none" stroke="#1e8fd6" stroke-width="1.5"><path d="M1 9h4v10H1zM5 10l4-8c2 0 2.5 1.5 2 3.5L10.5 8H17c1.3 0 2 1 1.7 2.3l-1.5 6.5c-.3 1.2-1 2-2.2 2H5"/></svg>10 Likes</span>
      <span><svg width="20" height="20" viewBox="0 0 20 20" fill="none" stroke="#1e8fd6" stroke-width="1.5"><path d="M1 2h17v11h-9l-4 4v-4H1zM4 6h11M4 9h9"/></svg>50 Comments</span>
    </div>
  </article>
</main>

<div class="page-code">C20</div>
</body>
</html>
```